business card

Business card for new business.
Red and black corporate colors.
Card can have an Indsutrial feel to it. Feel free to add Rust, Bolted steel, or graphics as you see fit. We provide highly specialized services to the below mentioned industries.
Keep information out of corners so that if I want I can choose rounded corners.
Information
- front. name - title - phone - email
- Rear
Refining - Rail - Infrastructure - Mining - Energy
Calgary - Edmonton - Fort McMurray - Revelstoke - Vancouver

```html
<!DOCTYPE html>
<html lang="en">
<head>
<meta charset="utf-8">
<title>Girderline business card</title>
<link rel="stylesheet" href="https://fonts.googleapis.com/css2?family=Roboto:wght@400;500&family=Roboto+Condensed:wght@700&display=swap">
<style>
  :root {
    --backdrop: #1f1f1f;
    --steel-light: #f2f2f2;
    --steel-mid: #dcdcdc;
    --steel-dark: #c4c4c4;
    --brand-red: #e30016;
    --ink-white: #ffffff;
    --ink-grey: #7a7a7a;
    --ink-list: #555555;
  }
  * { margin: 0; padding: 0; box-sizing: border-box; }
  html, body {
    width: 1200px; height: 960px; overflow: hidden;
    background: var(--backdrop);
    font-family: "Roboto", Arial, sans-serif;
  }
  .canvas { position: relative; width: 1200px; height: 960px; }
  .card {
    position: absolute; width: 600px; height: 343px; overflow: hidden;
    background: linear-gradient(90deg, var(--steel-dark) 0%, var(--steel-light) 30%, var(--steel-mid) 55%, var(--steel-light) 80%, var(--steel-dark) 100%);
  }
  .card--front { left: 314px; top: 113px; }
  .card--back { left: 311px; top: 472px; }

  .contact-band {
    position: absolute; left: 0; top: 98px; width: 283px; height: 146px;
    background: var(--brand-red); color: var(--ink-white);
    padding: 20px 0 0 29px;
  }
  .contact-band__name {
    font-family: "Roboto Condensed", Arial, sans-serif;
    font-weight: 700; font-size: 23px; line-height: 24px;
  }
  .contact-band__title { font-size: 15px; font-weight: 500; line-height: 20px; margin-top: 1px; }
  .contact-list { list-style: none; margin-top: 13px; }
  .contact-list li {
    display: flex; align-items: center; font-size: 14.5px; line-height: 19px;
  }
  .contact-list svg { width: 12px; height: 12px; margin-right: 10px; fill: var(--ink-white); }

  .wordmark {
    position: absolute; left: 323px; top: 148px;
    display: flex; align-items: center; gap: 10px;
  }
  .wordmark__square { width: 22px; height: 22px; background: var(--brand-red); }
  .wordmark__name {
    font-family: "Roboto Condensed", Arial, sans-serif;
    font-weight: 700; font-size: 44px; line-height: 48px; color: var(--ink-grey);
  }

  .brand-block {
    position: absolute; left: 170px; top: 125px; width: 108px; height: 108px;
    background: var(--brand-red);
  }
  .service-list {
    position: absolute; left: 301px; top: 77px; list-style: none;
    font-size: 14.5px; line-height: 19px; color: var(--ink-list);
  }
  .service-list li::before {
    content: "•"; color: var(--brand-red); display: inline-block; width: 11px;
  }
</style>
</head>
<body>
<main class="canvas">
  <section class="card card--front">
    <div class="contact-band">
      <h1 class="contact-band__name">MARCUS HALE</h1>
      <p class="contact-band__title">CEO/FOUNDER</p>
      <ul class="contact-list">
        <li><svg viewBox="0 0 24 24" aria-hidden="true"><path d="M6.6 10.8a15 15 0 0 0 6.6 6.6l2.2-2.2a1 1 0 0 1 1-.25 11.4 11.4 0 0 0 3.6.57 1 1 0 0 1 1 1V20a1 1 0 0 1-1 1A17 17 0 0 1 3 4a1 1 0 0 1 1-1h3.5a1 1 0 0 1 1 1c0 1.25.2 2.45.57 3.57a1 1 0 0 1-.25 1z"/></svg>604 555 0192</li>
        <li><svg viewBox="0 0 24 24" aria-hidden="true"><path d="M2 5h20v14H2z M4 7v.5l8 5 8-5V7l-8 5z" fill-rule="evenodd"/></svg>info@girderline.com</li>
        <li><svg viewBox="0 0 24 24" aria-hidden="true"><path d="M12 2a10 10 0 1 0 0 20 10 10 0 0 0 0-20zm-1 17.9A8 8 0 0 1 4.2 10l4.8 4.8v1a2 2 0 0 0 2 2zm6.9-2.5A2 2 0 0 0 16 16h-1v-3a1 1 0 0 0-1-1H8v-2h2a1 1 0 0 0 1-1V7h2a2 2 0 0 0 2-2v-.4a8 8 0 0 1 2.9 12.8z"/></svg>www.girderline.com</li>
      </ul>
    </div>
    <div class="wordmark">
      <span class="wordmark__square"></span>
      <span class="wordmark__name">GIRDERLINE</span>
    </div>
  </section>

  <section class="card card--back">
    <div class="brand-block"></div>
    <ul class="service-list">
      <li>Refining</li>
      <li>Rail</li>
      <li>Infrastructure</li>
      <li>Mining</li>
      <li>Energy</li>
      <li>Calgary</li>
      <li>Edmonton</li>
      <li>Fort McMurray</li>
      <li>Revelstoke</li>
      <li>Vancouver</li>
    </ul>
  </section>
</main>
</body>
</html>
```